German Headhunter/ HR Consultancy needs Business Cards Design

We need a business Card Design for our Company in Stuttgart. We are specialized as Headhunter/ HR Consultancy in Placement of specialist and managers in permanent employment. Please refer to our business logo.

```html
<!DOCTYPE html>
<html lang="de">
<head>
<meta charset="utf-8">
<title>Kernwerk Personalberatung – Visitenkarte</title>
<link rel="stylesheet" href="https://fonts.googleapis.com/css2?family=Montserrat:wght@600&family=Open+Sans:wght@400&display=swap">
<style>
  :root {
    --page-bg: #e9e7e7;
    --card-top-light: #f7f4f4;
    --card-top-warm: #ead9d9;
    --brand-blue: #3a56a8;
    --brand-grey: #939499;
    --divider-blue: #3a56a8;
    --text-light: #ffffff;
    --accent-soft: #eedcdc;
  }
  * { box-sizing: border-box; margin: 0; padding: 0; }
  html, body {
    width: 1200px; height: 900px; overflow: hidden;
    background: var(--page-bg);
  }
  .business-card {
    position: absolute; left: 100px; top: 141px;
    width: 1000px; height: 618px;
    box-shadow: 0 12px 40px rgba(0,0,0,0.18);
    overflow: hidden;
  }
  .card-header {
    position: absolute; left: 0; top: 0; width: 100%; height: 322px;
    background: radial-gradient(ellipse at 50% 40%, var(--card-top-light) 0%, var(--card-top-light) 45%, var(--card-top-warm) 100%);
    border-bottom: 2px solid var(--divider-blue);
    display: flex; align-items: center; justify-content: center;
  }
  .brand-lockup {
    display: flex; align-items: center; gap: 22px;
    margin-top: -30px;
  }
  .brand-square {
    width: 62px; height: 62px; background: var(--brand-blue);
  }
  .brand-name {
    font-family: "Montserrat", sans-serif; font-weight: 600;
    color: var(--brand-blue); line-height: 1;
  }
  .brand-name .primary { display: block; font-size: 64px; letter-spacing: 1px; }
  .brand-name .secondary { display: block; font-size: 28.5px; letter-spacing: 0.6px; margin-top: 6px; }
  .card-footer {
    position: absolute; left: 0; top: 322px; width: 100%; height: 296px;
    display: flex;
  }
  .contact-panel {
    position: relative; width: 560px; height: 100%;
    background: var(--brand-blue); color: var(--text-light);
    padding: 34px 0 0 49px;
  }
  .address-panel {
    flex: 1; height: 100%; background: var(--brand-grey);
    color: var(--text-light);
    display: flex; flex-direction: column; justify-content: flex-end;
    align-items: flex-end; text-align: right;
    padding: 0 46px 48px 0;
    font-family: "Open Sans", sans-serif; font-size: 26px; line-height: 36px;
  }
  .panel-divider {
    position: absolute; left: 560px; top: 322px; height: 296px;
  }
  .person-name {
    font-family: "Montserrat", sans-serif; font-weight: 600;
    font-size: 38px; letter-spacing: 0.3px; line-height: 1.1;
  }
  .person-role {
    font-family: "Open Sans", sans-serif; font-size: 27px; margin-top: 2px;
  }
  .contact-list { list-style: none; margin-top: 36px; }
  .contact-list li {
    display: flex; align-items: center; gap: 10px;
    font-family: "Open Sans", sans-serif; font-size: 27px; line-height: 36.5px;
  }
  .contact-list svg { width: 26px; height: 26px; flex: none; }
</style>
</head>
<body>
  <div class="business-card">
    <header class="card-header">
      <div class="brand-lockup">
        <div class="brand-square"></div>
        <div class="brand-name">
          <span class="primary">KERNWERK</span>
          <span class="secondary">PERSONALBERATUNG</span>
        </div>
      </div>
    </header>

    <section class="card-footer">
      <div class="contact-panel">
        <h1 class="person-name">LUKAS BRENNER</h1>
        <p class="person-role">Managing Director</p>
        <ul class="contact-list">
          <li>
            <svg viewBox="0 0 24 24" fill="none" stroke="#fff" stroke-width="2" stroke-linecap="round" stroke-linejoin="round"><path d="M5 3h4l2 5-2.5 1.5a11 11 0 0 0 6 6L16 13l5 2v4a2 2 0 0 1-2 2A17 17 0 0 1 3 5a2 2 0 0 1 2-2z"/></svg>
            0711-555 0192
          </li>
          <li>
            <svg viewBox="0 0 24 24" fill="none" stroke="#fff" stroke-width="2"><rect x="2" y="5" width="20" height="14"/><path d="M2 5l10 8 10-8"/></svg>
            kontakt@kernwerk-beratung.de
          </li>
          <li>
            <svg viewBox="0 0 24 24" fill="none" stroke="#fff" stroke-width="1.8"><circle cx="12" cy="12" r="10"/><ellipse cx="12" cy="12" rx="4.5" ry="10"/><path d="M2 12h20M4 7h16M4 17h16"/></svg>
            www.kernwerk-beratung.de
          </li>
        </ul>
      </div>
      <address class="address-panel" style="font-style: normal;">
        <span>Talstraße 18,</span>
        <span>Stuttgart-Ost</span>
        <span>70188, Germany</span>
      </address>
    </section>
  </div>
</body>
</html>
```